Web design for Crowdfunding site HopeWingsRally.com

We need a web design for christian crowdfunding website. Here is the challenge: We need responsive layout that is targeted first in iPad size of screen. It should also scale somehow down to iPhone size of screens. Web layout can be about the same size as iPad screen.

Screens should work so that main page scrolls not but only certain part of the screen scrolls and always one "page" at time. We can implement these "scrolls" then later with javascript but now we need only design. The challenge is to create this kind of hybrid website / app look.

Target is at first to raise funds to orphan people needing about $40 per month for their living and education. There is always some organization which takes care of these kids. Later there will be other christian missions included. At first we are looking to find monthly supporters.

You can be as creative as you want :) As you see from the look and feel sector, I am not looking any same traditional look which many "help kids" sites have. I am looking to reach now younger generation and therefore iPad and mobile are the main screen sizes.

Inspirational designs:
- https://example-gallery.test/profiles/studiofernlake/designs/482716?from=%2Fbrowse%2Fxhr%2Fdesigns%3Fcategory%3Dmobile-app-design
- http://www.artpoolhub.test/design/8261047 Clear, simple visuals
- http://www.artpoolhub.test/design/7394215 Header
- http://www.artpoolhub.test/design/6048392 Contrast in the colors, i think is powerfull

Some terms could be: Kids play, kids are learning (in the school). No static posture but living like kids are. I wonder also how we could also add little bit gaming style even though the question is of reali life of real people. Giving should be rewarding.

Target Market(s)

People who want help other people.

Industry/Entity Type

Christian

Number of Pages Required

4 page

Requirements
Must have
• Homepage. Mission page (In my wireframes it was one kid).
Nice to have
• Other pages and some idea how to scroll. 4 pages is no must. If you feel easy, please give first some draft and I give comments on that.

```html
<!DOCTYPE html>
<html lang="en">
<head>
<meta charset="utf-8">
<title>HopeWingsRally – Welcome</title>
<link rel="stylesheet" href="https://fonts.googleapis.com/css2?family=Raleway:wght@500;600;700&family=Open+Sans:wght@400&display=swap">
<style>
  :root {
    --ink: #ffffff;
    --night: #0b0b0b;
    --footer: #0e0e0e;
    --red: #e8302f;
    --yellow: #fcbb00;
    --gold-btn: #8c6c00;
    --red-btn: #8a1c1c;
    --dot-active: #f4b400;
    --ring: #8a8a8a;
    --ring-fill: #1c1c1c;
    --muted: #b5b5b5;
    --map-grey: #a9a9a9;
    --jar-orange: #f39a2e;
    --note-green: #4f9a55;
  }
  * { box-sizing: border-box; margin: 0; padding: 0; }
  html, body { width: 1200px; height: 900px; overflow: hidden; background: var(--night); }
  body { position: relative; font-family: "Raleway", sans-serif; color: var(--ink); }

  .hero-backdrop {
    position: absolute; left: 0; top: 0; width: 1200px; height: 824px;
    background:
      radial-gradient(ellipse at 75% 70%, rgba(90,45,25,0.45), transparent 55%),
      radial-gradient(ellipse at 25% 30%, rgba(50,50,55,0.55), transparent 55%),
      linear-gradient(180deg, #121212 0%, #1a1816 55%, #0c0c0c 100%);
  }

  .site-header { position: absolute; left: 0; top: 0; width: 1200px; height: 78px; }
  .nav-missions {
    position: absolute; left: 42px; top: 30px; display: flex; align-items: center; gap: 10px;
    font-size: 16px; font-weight: 700;
  }
  .nav-search { position: absolute; left: 259px; top: 29px; }
  .brand { position: absolute; left: 440px; top: 0; height: 78px; display: flex; align-items: center; }
  .brand-square { width: 77px; height: 78px; background: var(--red); }
  .brand-name { margin-left: 12px; font-size: 27px; font-weight: 600; letter-spacing: 1px; }
  .nav-account { position: absolute; top: 30px; font-size: 16px; font-weight: 600; }
  .nav-login { left: 996px; }
  .nav-signup { left: 1094px; }

  .welcome-band {
    position: absolute; left: 0; top: 325px; width: 568px; height: 71px;
    background: var(--red); clip-path: polygon(0 0, 100% 0, 95.5% 100%, 0 100%);
    display: flex; align-items: center; padding-left: 42px;
  }
  .welcome-band h1 { font-size: 35px; font-weight: 700; }

  .pitch-band {
    position: absolute; left: 0; top: 411px; width: 568px; height: 165px;
    background: var(--yellow); clip-path: polygon(0 0, 100% 0, 89.8% 100%, 0 100%);
    padding: 28px 0 0 41px;
  }
  .pitch-band p { font-size: 22px; line-height: 35px; font-weight: 500; }
  .pitch-band strong { font-weight: 700; }

  .hero-illustration {
    position: absolute; left: 612px; top: 190px; width: 560px; height: 488px;
    border-radius: 28px;
    background: linear-gradient(140deg, var(--note-green) 0%, var(--map-grey) 35%, var(--jar-orange) 70%, #d8672a 100%);
    opacity: 0.85;
  }

  .quick-link {
    position: absolute; left: 0; width: 227px; height: 63px;
    display: flex; align-items: center; gap: 18px; padding-left: 12px;
    font-size: 26px; font-weight: 500; letter-spacing: 1px;
  }
  .quick-contact { top: 685px; background: var(--gold-btn); }
  .quick-services { top: 762px; background: var(--red-btn); }

  .slide-dots { position: absolute; left: 555px; top: 748px; display: flex; gap: 6px; }
  .slide-dots span { width: 19px; height: 19px; border-radius: 50%; background: var(--ink); }
  .slide-dots span.is-active { background: var(--dot-active); }

  .slide-code { position: absolute; left: 1163px; top: 792px; font-family: "Open Sans", sans-serif; font-size: 15px; }

  .site-footer { position: absolute; left: 0; top: 824px; width: 1200px; height: 76px; background: var(--footer); }
  .copyright {
    position: absolute; left: 43px; top: 27px; font-family: "Open Sans", sans-serif;
    font-size: 16px; color: var(--muted);
  }
  .social-links { position: absolute; left: 973px; top: 18px; display: flex; gap: 8px; }
  .social-links span {
    width: 41px; height: 41px; border-radius: 50%; border: 2px solid var(--ring);
    background: radial-gradient(circle, var(--ring) 0 6px, var(--ring-fill) 7px);
  }
</style>
</head>
<body>
  <div class="hero-backdrop" role="img" aria-label="Dark blurred photo of a crowd gathered together"></div>

  <header class="site-header">
    <div class="nav-missions">
      <svg width="16" height="13" viewBox="0 0 16 13" aria-hidden="true">
        <g fill="#fff">
          <rect x="0" y="0" width="3" height="3"/><rect x="5" y="0" width="11" height="3"/>
          <rect x="0" y="5" width="3" height="3"/><rect x="5" y="5" width="11" height="3"/>
          <rect x="0" y="10" width="3" height="3"/><rect x="5" y="10" width="11" height="3"/>
        </g>
      </svg>
      SEE THE MISSIONS
    </div>
    <svg class="nav-search" width="21" height="21" viewBox="0 0 21 21" aria-label="Search">
      <circle cx="8.5" cy="8.5" r="6.5" fill="none" stroke="#fff" stroke-width="3"/>
      <line x1="13.5" y1="13.5" x2="19" y2="19" stroke="#fff" stroke-width="3.5" stroke-linecap="round"/>
    </svg>

    <div class="brand">
      <div class="brand-square"></div>
      <span class="brand-name">HOPEWINGSRALLY</span>
    </div>

    <div class="nav-account nav-login">LOGIN</div>
    <div class="nav-account nav-signup">SIGN UP</div>
  </header>

  <div class="welcome-band"><h1>Welcome to HopeWingsRally</h1></div>
  <div class="pitch-band">
    <p>She has a name. he has dreams. She hopes<br>she would have a future. he is like you.<br><strong>1 USD a month will help her and him.</strong></p>
  </div>

  <div class="hero-illustration" role="img" aria-label="Flat illustration of people around a world map holding banknotes over a donation jar"></div>

  <div class="quick-link quick-contact">
    <svg width="24" height="24" viewBox="0 0 24 24" aria-hidden="true">
      <path fill="#fff" d="M6.6 10.8a15.1 15.1 0 0 0 6.6 6.6l2.2-2.2c.3-.3.7-.4 1-.2 1.1.4 2.3.6 3.6.6.6 0 1 .4 1 1V20c0 .6-.4 1-1 1A17 17 0 0 1 3 4c0-.6.4-1 1-1h3.5c.6 0 1 .4 1 1 0 1.3.2 2.5.6 3.6.1.3 0 .7-.2 1l-2.3 2.2z"/>
    </svg>
    CONTACT
  </div>
  <div class="quick-link quick-services">
    <svg width="28" height="20" viewBox="0 0 28 20" aria-hidden="true">
      <rect x="1.5" y="1.5" width="25" height="17" rx="2" fill="none" stroke="#fff" stroke-width="3"/>
      <circle cx="14" cy="10" r="4.5" fill="#fff"/>
    </svg>
    SERVICES
  </div>

  <div class="slide-dots">
    <span class="is-active"></span><span></span><span></span><span></span>
  </div>
  <div class="slide-code">C4</div>

  <footer class="site-footer">
    <p class="copyright">© 2016 HopeWingsRally. All rights reserved.Privacy &amp; Legal Policy</p>
    <div class="social-links" aria-label="Social links">
      <span></span><span></span><span></span><span></span>
    </div>
  </footer>
</body>
</html>
```